TL - business card

Tallow Partners is an insurance brokerage firm, inovative, proactive, vigorous, which aims to become the leader of the insurance brokers in Anfrica. We should like to get some designs which should be avoided also in Gray / Metallic for the Administration and Orange / Blue for the Managers (ike in the picture sent). The Blue / Green logo is not the correct one, but the source of the file. Please adjust the color accordingly for the business cards. 1 / Orange / Blue 2 / Gray / Metallic We want something classic but which is transmitted strenght, inovation, modernity and most of all, rapidity. We want something start-up like, very punchy and catching eye remaining profesional at the same time. Name: Dorian Whitlock Function: Managing Director Address: N ° 17/18 Rua Veloso - R / C 2B Direita - Bairro Mutamba - Luanda Tel: (+244) 947 582 316 Email: dorian.whitlock@tallow-p.example Website: www.tallow-p. example We want classic in the front and creative, colorfull at the back. The cards will be printed in relief, with very high quality of paper.
Insurance Broker
Colors
Designer to choose colors to be used in the design.

```html
<!DOCTYPE html>
<html lang="en">
<head>
<meta charset="utf-8">
<title>Tallow Partners – Business Card</title>
<link rel="stylesheet" href="https://fonts.googleapis.com/css2?family=Montserrat:wght@300;400;500;600&display=swap">
<style>
  :root {
    --backdrop: #121212;
    --card: #1d1d1d;
    --card-light: #262626;
    --silver: #d9d9d9;
    --silver-soft: #b5b5b5;
    --emboss: #2c2c2c;
    --rule: #4a4a4a;
  }
  * { margin: 0; padding: 0; box-sizing: border-box; }
  html, body { width: 1200px; height: 900px; overflow: hidden; }
  body {
    background: radial-gradient(ellipse at 60% 30%, #232323 0%, var(--backdrop) 70%);
    font-family: "Montserrat", sans-serif;
    position: relative;
  }
  .card {
    position: absolute;
    left: 280px;
    width: 640px;
    height: 366px;
    background: linear-gradient(135deg, var(--card) 0%, var(--card-light) 60%, var(--card) 100%);
    box-shadow: 0 18px 40px rgba(0,0,0,0.6);
  }
  .card--front { top: 62px; }
  .card--back { top: 472px; }

  .brand {
    position: absolute;
    inset: 0;
    display: flex;
    align-items: center;
    justify-content: center;
    gap: 18px;
  }
  .brand__dot {
    width: 46px; height: 46px;
    border-radius: 50%;
    border: 4px solid var(--silver-soft);
  }
  .brand__name {
    font-weight: 600;
    font-size: 34px;
    letter-spacing: 1px;
    color: var(--silver);
    text-transform: uppercase;
  }

  .back__mark {
    position: absolute;
    left: 52px; top: 78px;
    width: 210px; height: 210px;
    border-radius: 50%;
    border: 10px solid var(--emboss);
    box-shadow: inset 1px 1px 2px rgba(255,255,255,0.06), 1px 1px 2px rgba(0,0,0,0.6);
  }
  .back__rule {
    position: absolute;
    left: 318px; top: 70px;
    width: 1px; height: 226px;
    background: var(--rule);
  }
  .contact {
    position: absolute;
    left: 350px; top: 78px;
    color: var(--silver-soft);
  }
  .contact__name {
    font-weight: 500;
    font-size: 27px;
    letter-spacing: 1px;
    color: var(--silver);
  }
  .contact__role {
    font-weight: 400;
    font-size: 15px;
    margin-top: 2px;
    margin-bottom: 16px;
  }
  .contact__address {
    font-weight: 400;
    font-size: 16px;
    line-height: 1.4;
    margin-bottom: 12px;
  }
  .contact__line {
    display: flex;
    align-items: center;
    gap: 10px;
    font-size: 16px;
    line-height: 1.55;
  }
  .contact__line svg { width: 13px; height: 13px; flex: none; }
</style>
</head>
<body>
  <section class="card card--front">
    <div class="brand">
      <span class="brand__dot"></span>
      <span class="brand__name">Tallow Partners</span>
    </div>
  </section>

  <section class="card card--back">
    <div class="back__mark"></div>
    <div class="back__rule"></div>
    <div class="contact">
      <p class="contact__name">Dorian Whitlock</p>
      <p class="contact__role">Managing Director</p>
      <p class="contact__address">N ° 17/18 Rua Veloso<br>R / C 2B Direita<br>Bairro Mutamba - Luanda</p>
      <p class="contact__line">
        <svg viewBox="0 0 16 16" aria-hidden="true"><path d="M3 1.5 L6 1.5 L7 5 L5.3 6.3 Q6.8 9.4 9.7 10.7 L11 9 L14.5 10 L14.5 13 Q14.5 14.5 13 14.5 Q2 13.5 1.5 3 Q1.5 1.5 3 1.5 Z" fill="none" stroke="#b5b5b5" stroke-width="1.3"/></svg>
        +244 947 582 316
      </p>
      <p class="contact__line">
        <svg viewBox="0 0 16 16" aria-hidden="true"><rect x="1.5" y="3.5" width="13" height="9" fill="none" stroke="#b5b5b5" stroke-width="1.3"/><path d="M1.5 3.5 L8 9 L14.5 3.5" fill="none" stroke="#b5b5b5" stroke-width="1.3"/></svg>
        dorian.whitlock@tallow-p.example
      </p>
    </div>
  </section>
</body>
</html>
```